To design a brand identity that is simple and creative with 'Corvane' as the brand name, I like modern simple fonts like helvetica neue, I want to print both sides of the card, I am open to dark front and white back, but the design needs to transfer well to letter heads and email signatures, I am looking for sophisticated and elegant, but open minded about clever and off the wall, I do not do 'boring' Corvane Ventures is the mother company for a small group, specialising in Management & consulting, Software development and construction, we have a high level of integrity, we are transparent and accountable for what we do. my images are provided as a guide only, Im not expecting them to be just copied, Im looking for a creator and passionate thinker, who will put life into their work.

Target Market(s)

usually business minded people who are looking for something different in me, such as leadership, confidence and focus with thinking that is per haps a little outside the box..

Industry/Entity Type

Construction

Requirements
Must have
• clean, minmalistic
Nice to have
• custom logo
Should not have
• boring, traditional

```html
<!DOCTYPE html>
<html lang="en">
<head>
<meta charset="utf-8">
<title>Corvane — Business Card</title>
<link rel="stylesheet" href="https://fonts.googleapis.com/css2?family=Inter:wght@200;300;400&display=swap">
<style>
  :root {
    --stage: #2f2c2a;
    --card-white: #f4f4f5;
    --brand-red: #bf3341;
    --dot-red: #cc3340;
    --brand-orange: #d8653c;
    --ink-dark: #2a2a2a;
    --ink-grey: #8a8a8a;
    --ghost-grey: #dedee0;
    --back-light: #555454;
    --back-dark: #262626;
    --white: #ffffff;
  }
  * { box-sizing: border-box; margin: 0; padding: 0; }
  html, body {
    width: 1000px; height: 1200px; overflow: hidden;
    background: var(--stage);
    font-family: "Inter", "Helvetica Neue", Arial, sans-serif;
  }
  .card {
    position: absolute;
    width: 740px; height: 457px;
    overflow: hidden;
  }
  /* Front */
  .card-front { left: 136px; top: 75px; background: var(--card-white); }
  .front-band { position: absolute; inset: 0; width: 100%; height: 100%; }
  .contact { position: absolute; left: 44px; top: 139px; color: var(--white); }
  .contact-name { font-size: 23px; font-weight: 400; line-height: 1; }
  .contact-role { font-size: 15px; font-weight: 400; margin-top: 7px; }
  .contact-list { list-style: none; font-size: 15px; font-weight: 300; margin-top: 12px; letter-spacing: .2px; }
  .contact-list li { line-height: 28px; }
  .contact-list li.gap { margin-top: 14px; }
  .ghost-name {
    position: absolute; left: 338px; top: 112px;
    writing-mode: vertical-rl; transform: rotate(180deg);
    font-size: 64px; font-weight: 300; color: var(--ghost-grey);
    line-height: 1;
  }
  .services-vertical {
    position: absolute; left: 357px; top: 55px; height: 345px;
    writing-mode: vertical-rl; transform: rotate(180deg);
    font-size: 15px; font-weight: 400; color: var(--ink-dark);
    letter-spacing: .8px; white-space: nowrap;
  }
  .dot { color: var(--dot-red); padding: 0 5px; }
  .brand-small { position: absolute; right: 44px; top: 348px; text-align: right; }
  .brand-small .wordmark {
    display: inline-flex; align-items: center; gap: 14px;
    font-size: 38px; font-weight: 300; color: var(--brand-orange); line-height: 1;
  }
  .brand-mark { display: inline-block; border-radius: 50%; background: var(--brand-orange); }
  .brand-small .brand-mark { width: 26px; height: 26px; }
  .tagline { font-size: 11px; font-weight: 300; color: var(--ink-grey); margin-top: 10px; letter-spacing: .4px; }
  /* Back */
  .card-back {
    left: 117px; top: 652px;
    background: radial-gradient(ellipse 60% 70% at 50% 40%, var(--back-light), var(--back-dark));
  }
  .brand-large { position: absolute; left: 0; right: 0; top: 180px; text-align: center; }
  .brand-large .wordmark {
    display: inline-flex; align-items: center; gap: 26px;
    font-size: 96px; font-weight: 300; color: var(--white); line-height: 1;
  }
  .brand-large .brand-mark { width: 60px; height: 60px; background: var(--white); }
  .services-line {
    margin-top: 20px; font-size: 15px; font-weight: 300; color: var(--white); letter-spacing: 1.5px;
  }
  .services-line .dot { padding: 0 3px; }
</style>
</head>
<body>
  <section class="card card-front" aria-label="Business card front">
    <svg class="front-band" viewBox="0 0 740 457" preserveAspectRatio="none" aria-hidden="true">
      <polygon points="0,0 329,0 236,457 0,457" fill="var(--brand-red)"/>
    </svg>
    <div class="contact">
      <h1 class="contact-name">Alex Marlow</h1>
      <p class="contact-role">client ambassador</p>
      <ul class="contact-list">
        <li>c. +61 0400 555 192</li>
        <li>e. info@corvane.com.au</li>
        <li class="gap">a. po box 418 perth 6100</li>
        <li>w. www.corvane.com.au</li>
      </ul>
    </div>
    <span class="ghost-name" aria-hidden="true">Corvane</span>
    <p class="services-vertical">management<span class="dot">•</span>software<span class="dot">•</span>construction</p>
    <div class="brand-small">
      <div class="wordmark"><span class="brand-mark" aria-hidden="true"></span>Corvane</div>
      <p class="tagline">built on clear thinking</p>
    </div>
  </section>

  <section class="card card-back" aria-label="Business card back">
    <div class="brand-large">
      <div class="wordmark"><span class="brand-mark" aria-hidden="true"></span>Corvane</div>
      <p class="services-line">management <span class="dot">•</span> software <span class="dot">•</span> construction</p>
    </div>
  </section>
</body>
</html>
```